Melorix artwork for new single release

I need Melorix artwork creating to release a new single on there.

The specs are:

Ideal size: 3000 x 3000 pixels
Minimum size: 1400 x 1400 pixels
Aspect ratio: 1:1 (must be a perfect square)
File format: JPG or PNG
Color space: sRGB
File size: Max 4MB

The song is called "Was It Ever Rain?"
The artist is "Martin Hollow"

We have no images of Martin, so it really is open to imagination.

Target Market(s)

Melorix listeners

Industry/Entity Type

Music

```html
<!DOCTYPE html>
<html lang="en">
<head>
<meta charset="utf-8">
<title>Was It Ever Rain? — Martin Hollow</title>
<link rel="stylesheet" href="https://fonts.googleapis.com/css2?family=Figtree:wght@800&display=swap">
<style>
  :root {
    --sky-top: #0f2a40;
    --sky-mid: #2b6a80;
    --horizon: #c49a9a;
    --water: #3a3a44;
    --ground: #3b2a2c;
    --ground-dark: #1f1719;
    --title-ink: #f6f3e6;
    --glow: #ff7a2a;
  }
  html, body {
    margin: 0;
    padding: 0;
    width: 1200px;
    height: 1200px;
    overflow: hidden;
    background: #000;
  }
  .cover {
    position: relative;
    width: 1200px;
    height: 1200px;
    overflow: hidden;
    font-family: "Figtree", "Helvetica Neue", Arial, sans-serif;
  }
  .cover__scene {
    position: absolute;
    inset: 0;
    background:
      radial-gradient(ellipse 200px 220px at 600px 480px, rgba(255,122,42,0.35), transparent 70%),
      linear-gradient(to bottom,
        var(--sky-top) 0%,
        var(--sky-mid) 30%,
        var(--horizon) 47%,
        #8a5a3e 54%,
        var(--water) 58%,
        #2a2530 80%,
        var(--ground) 83%,
        var(--ground-dark) 100%);
  }
  .cover__title,
  .cover__artist {
    position: absolute;
    left: 0;
    right: 0;
    margin: 0;
    text-align: center;
    color: var(--title-ink);
    font-weight: 800;
    text-transform: uppercase;
    letter-spacing: 0.03em;
    line-height: 1;
  }
  .cover__title {
    top: 88px;
    font-size: 68px;
  }
  .cover__artist {
    top: 1040px;
    font-size: 60px;
  }
</style>
</head>
<body>
  <main class="cover">
    <div class="cover__scene" role="img" aria-label="Night riverside scene under a starry sky with lamplit buildings and a stone bridge; a silhouetted man stands on cobblestones with his hand over a glowing orange heart on his chest"></div>
    <h1 class="cover__title">Was It Ever Rain?</h1>
    <p class="cover__artist">Martin Hollow</p>
  </main>
</body>
</html>
```